label design peanut butter jar to be marketed internationally for a singapore based company

We need design of 2 labels creamy peanut butter and crunch peanut butter
The design is the same only photo of product
And wording change
The logo nordvel remains the same and has to be used logo of peanut has to be used
Some idea designs by our in house designer
Enclosed .
Plus a design of a competitor lunar meadow

Target Market(s)

international specially emerging markets

Industry/Entity Type

It Company

Requirements
Must have
• nordvel logo
• peanut logo

```html
<!DOCTYPE html>
<html lang="en">
<head>
<meta charset="utf-8">
<title>Nordvel Creamy Peanut Butter – Label</title>
<link rel="stylesheet" href="https://fonts.googleapis.com/css2?family=Arimo:wght@700&display=swap">
<style>
  :root {
    --purple: #5f3d8e;
    --purple-text: #5a3a8a;
    --orange: #f26a22;
    --orange-deep: #ee5f1c;
    --yellow: #f6e60f;
    --white: #ffffff;
    --page: #ffffff;
  }
  html, body {
    margin: 0;
    padding: 0;
    width: 871px;
    height: 1200px;
    overflow: hidden;
    background: var(--page);
  }
  .canvas {
    position: relative;
    width: 871px;
    height: 1200px;
  }
  .label {
    position: absolute;
    left: 128px;
    top: 410px;
    width: 617px;
    height: 546px;
  }
  .label svg { display: block; }
  .brand-name {
    font-family: "Arimo", Arial, sans-serif;
    font-weight: 700;
    font-size: 60px;
    letter-spacing: 9px;
    fill: var(--purple-text);
  }
  .brand-mark { fill: var(--orange); }
  .product-title {
    font-family: "Arimo", Arial, sans-serif;
    font-weight: 700;
    fill: var(--purple-text);
  }
  .net-weight {
    font-family: "Arimo", Arial, sans-serif;
    font-weight: 700;
    font-size: 15px;
    fill: var(--white);
    letter-spacing: 0.5px;
  }
</style>
</head>
<body>
<main class="canvas">
  <section class="label">
    <svg width="617" height="546" viewBox="0 0 617 546" xmlns="http://www.w3.org/2000/svg">
      <defs>
        <clipPath id="label-area"><rect x="0" y="0" width="617" height="546"/></clipPath>
        <radialGradient id="sunburst" cx="0.5" cy="0.55" r="0.55">
          <stop offset="0" stop-color="#fbe33a"/>
          <stop offset="0.45" stop-color="#f8b523"/>
          <stop offset="1" stop-color="#f27e22"/>
        </radialGradient>
        <radialGradient id="product-tone" cx="0.5" cy="0.45" r="0.6">
          <stop offset="0" stop-color="#d9a468"/>
          <stop offset="1" stop-color="#c08346"/>
        </radialGradient>
      </defs>

      <g clip-path="url(#label-area)">
        <rect class="label-field" x="0" y="0" width="617" height="546" fill="var(--orange)"/>

        <ellipse class="ring-yellow" cx="309" cy="262" rx="318" ry="232" fill="var(--yellow)"/>
        <ellipse class="ring-orange" cx="309" cy="262" rx="311" ry="225" fill="var(--orange-deep)"/>
        <ellipse class="ring-purple" cx="309" cy="264" rx="304" ry="218" fill="var(--purple)"/>
        <ellipse class="sunburst" cx="309" cy="266" rx="292" ry="206" fill="url(#sunburst)"/>

        <path class="top-band" d="M0 0 H617 V24 Q309 40 0 24 Z" fill="var(--purple)"/>

        <ellipse class="product-photo" role="img" aria-label="Photo of a spoon heaped with creamy peanut butter"
                 cx="290" cy="280" rx="175" ry="105" fill="url(#product-tone)"/>

        <path class="bottom-band" d="M0 458 Q309 474 617 458 V546 H0 Z" fill="var(--purple)"/>
      </g>

      <g class="brand-badge">
        <ellipse cx="309" cy="105" rx="222" ry="72" fill="var(--orange)"/>
        <ellipse cx="309" cy="105" rx="214" ry="65" fill="var(--white)"/>
        <text class="brand-name" x="290" y="127" text-anchor="middle">NORDVEL</text>
        <circle class="brand-mark" cx="475" cy="108" r="15"/>
      </g>

      <g class="product-badge">
        <ellipse cx="304" cy="448" rx="204" ry="62" fill="var(--orange)"/>
        <ellipse cx="304" cy="448" rx="196" ry="55" fill="var(--white)"/>
        <text class="product-title" x="304" y="444" text-anchor="middle" font-size="42" textLength="222" lengthAdjust="spacingAndGlyphs">CREAMY</text>
        <text class="product-title" x="304" y="478" text-anchor="middle" font-size="30" textLength="296" lengthAdjust="spacingAndGlyphs">PEANUT BUTTER</text>
      </g>

      <text class="net-weight" x="304" y="535" text-anchor="middle">200 GRAMS</text>
    </svg>
  </section>
</main>
</body>
</html>
```